Web page for a garment manufacturing company

We are clothing manufacturer based in Romania.
With our recent expansion, we have significantly increased our internal capacity, allowing us to take on new partnerships and deliver high-quality production services.
Our expertise includes producing classic coats, blazers, trousers, skirts, dresses, and blouses, though we are flexible and open to working with various other textile products.

Target Market(s)

High-end market and luxury

Industry/Entity Type

Garments Manufacturer

Coding

Coded - Design and coding required

Number of Pages Required

1 page

Colors

Designer to choose only greyscale colors for use in the design.

Requirements
Must have
• Velmora logo from our presentation
Nice to have
• https://www.lorvani.pt/
Should not have
• prices, wedding dresses, collections

```html
<!DOCTYPE html>
<html lang="en">
<head>
<meta charset="utf-8">
<title>Velmora – Quality in Every Stitch</title>
<link href="https://fonts.googleapis.com/css2?family=Poppins:wght@300;400;500;600;700&display=swap" rel="stylesheet">
<style>
:root{
  --accent:#3a3a3a;
  --accent-soft:#6a6a6a;
  --page:#e4e4e4;
  --ink:#1c1c1c;
  --white:#ffffff;
  --muted:#8a8a8a;
  --card:#efefef;
  --pill:#e6e6e6;
}
*{box-sizing:border-box;margin:0;padding:0}
html,body{width:1200px;height:3952px;overflow:hidden}
body{background:var(--page);font-family:'Poppins',sans-serif;color:var(--ink);position:relative}
.abs{position:absolute}
.hero{left:0;top:0;width:1200px;height:798px;
  background:linear-gradient(180deg,#9a9a9a 0%,#c8c8c8 20%,#b0b0b0 35%,#7a7a7a 52%,#404040 72%,#2a2a2a 100%)}
.logo{left:100px;top:30px;font-size:42px;font-weight:300;color:var(--ink);letter-spacing:-1px}
.nav{left:293px;top:46px;font-size:18px;font-weight:400}
.nav a{color:var(--ink);text-decoration:none;position:absolute;white-space:nowrap}
.lang{left:1010px;top:40px;width:104px;height:34px;border-radius:17px;background:var(--accent);color:var(--white);font-size:17px;display:flex;align-items:center;justify-content:center;gap:8px}
.headline{left:101px;top:140px;font-size:64px;font-weight:600;line-height:90px;white-space:nowrap}
.headline .dark{color:var(--ink)}
.headline .soft{color:#4f4f4f}
.swoosh{left:92px;top:205px}
.btn-hero{left:101px;top:351px;width:158px;height:48px;border-radius:24px;background:var(--accent);font-size:19px;font-weight:500;display:flex;align-items:center;justify-content:center;color:var(--white)}
.infobar{left:221px;top:752px;width:757px;height:84px;border-radius:24px;background:var(--white)}
.info{position:absolute;top:14px;font-size:16px;white-space:nowrap}
.info .label{color:var(--muted);font-size:15px;display:flex;align-items:center;gap:6px;margin-bottom:8px}
.section-title{width:1200px;text-align:center;font-size:34px;font-weight:500}
.photo{border-radius:14px;border:1.5px solid #333;overflow:hidden}
.dark-card{background:var(--accent);border-radius:22px;color:var(--white)}
.pill{background:var(--pill);color:var(--ink);border-radius:8px;font-size:15px;display:flex;align-items:center;justify-content:center}
.tabs{left:296px;top:2034px;width:616px;height:50px;background:#d8d8d8;border-radius:12px;font-size:15px}
.tabs span{position:absolute;top:14px;white-space:nowrap}
.tab-active{left:494px;top:4px;width:118px;height:42px;background:#ececec;border-radius:10px}
.gallery-card{top:2164px;width:248px;height:396px;background:var(--card);border-radius:12px;overflow:hidden}
.gallery-card .img{height:281px}
.gallery-card h3{font-size:19px;font-weight:600;margin:18px 0 0 24px}
.gallery-card p{font-size:14px;margin:10px 18px 0 24px;line-height:21px}
.sustain{left:75px;top:2655px;width:1044px;height:349px;border:2px solid var(--accent);background:var(--white);overflow:hidden}
.sustain h2{position:absolute;left:63px;top:38px;font-size:41px;font-weight:600;line-height:58px;color:var(--white)}
.bullet{position:absolute;font-size:24px;font-weight:600;color:var(--white);line-height:34px}
.bullet::before{content:"•";position:absolute;left:-22px}
.more{position:absolute;left:795px;top:44px;font-size:31px;font-weight:400;line-height:46px;color:var(--ink)}
.btn-dark{background:var(--accent);border-radius:20px;color:var(--white);display:flex;align-items:center;justify-content:center;box-shadow:0 3px 4px rgba(0,0,0,.2)}
.feedback{left:307px;top:3067px;width:629px;height:513px;border:2px solid var(--accent);background:var(--white)}
.feedback h2{text-align:center;margin-top:36px;font-size:31px;font-weight:500}
.field{position:absolute;left:60px;width:508px;border:1.5px solid var(--accent-soft);color:#b5b5b5;font-size:19px;padding:10px 14px;font-weight:300}
.footer{left:0;top:3632px;width:1200px;height:320px;background:var(--accent);color:var(--white);font-size:19px}
.footer .flogo{position:absolute;left:72px;top:20px;font-size:46px;font-weight:300;color:var(--white)}
.footer .row{position:absolute;display:flex;gap:14px;align-items:flex-start;line-height:28px;white-space:nowrap}
.footer .links{position:absolute;left:579px;top:98px;line-height:28px}
.social{position:absolute;top:196px;width:40px;height:40px;border-radius:50%;background:var(--white)}
.copy{position:absolute;top:274px;width:1200px;text-align:center;color:var(--white);font-size:19px}
</style>
</head>
<body>

<header class="abs hero" role="img" aria-label="Photo of a city skyline of tall towers at sunset"></header>
<div class="abs logo">Velmora</div>
<nav class="abs nav">
  <a style="left:0">About Us</a>
  <a style="left:114px">Velmora</a>
  <a style="left:203px">Sustainability</a>
  <a style="left:350px">Contact</a>
</nav>
<div class="abs lang">
  <svg width="20" height="18" viewBox="0 0 20 18"><rect x="1" y="1" width="11" height="11" rx="2" fill="none" stroke="#fff" stroke-width="1.6"/><rect x="8" y="6" width="11" height="11" rx="2" fill="#fff"/></svg>
  EN
  <svg width="10" height="6" viewBox="0 0 10 6"><path d="M0 0h10L5 6z" fill="#fff"/></svg>
</div>
<div class="abs headline"><span class="dark">Quality</span> <span class="soft">in</span><br><span class="dark">Every</span> <span class="soft">Stitch</span></div>
<svg class="abs swoosh" width="250" height="30" viewBox="0 0 250 30"><path d="M2 26 Q120 10 240 4" stroke="#3a3a3a" stroke-width="4" fill="none" stroke-linecap="round"/></svg>
<div class="abs btn-hero">Contact Us</div>

<div class="abs infobar">
  <div class="info" style="left:32px">
    <div class="label"><svg width="16" height="16" viewBox="0 0 24 24"><path d="M6 2l4 4-2 3c1 2 4 5 6 6l3-2 4 4-3 3C10 20 4 14 3 5z" fill="none" stroke="#8a8a8a" stroke-width="2"/></svg>Telephone</div>
    +4(0) 300 555 018
  </div>
  <div class="info" style="left:282px;text-align:center">
    <div class="label" style="justify-content:center"><svg width="16" height="14" viewBox="0 0 24 18"><rect x="1" y="1" width="22" height="16" rx="2" fill="none" stroke="#8a8a8a" stroke-width="2"/><path d="M1 2l11 8 11-8" fill="none" stroke="#8a8a8a" stroke-width="2"/></svg>Email</div>
    info@velmorafashion.com
  </div>
  <div class="info" style="left:591px;text-align:center">
    <div class="label" style="justify-content:center">Location</div>
    Valeni, Dumbrava,
  </div>
</div>

<h2 class="abs section-title" style="left:0;top:895px">About Us</h2>
<div class="abs dark-card" style="left:74px;top:998px;width:515px;height:400px">
  <p style="position:absolute;left:39px;top:58px;width:450px;font-size:19px;line-height:28px">VELMORA is a manufacturing company for Ready-to-wear, situated in Valeni, a city with a rich tradition in the clothing industry. The top management is international, and we are proud to have a diverse and dynamic group of professionals from different countries working together.</p>
  <div class="abs pill" style="left:39px;top:315px;width:132px;height:37px">View More</div>
</div>
<div class="abs photo" style="left:606px;top:998px;width:252px;height:400px;background:linear-gradient(160deg,#707070,#3b3b3b 60%,#808080)" role="img" aria-label="Photo of knitwear hanging on clothing racks"></div>
<div class="abs photo" style="left:873px;top:998px;width:252px;height:400px;background:linear-gradient(180deg,#8f8f8f 0%,#b8b8b8 45%,#4a4a4a 75%,#383838)" role="img" aria-label="Photo of light dresses on a rail"></div>
<div class="abs photo" style="left:74px;top:1424px;width:250px;height:399px;background:linear-gradient(180deg,#d8d8d8,#363636 55%,#999)" role="img" aria-label="Photo of a dark knit cardigan on a hanger"></div>
<div class="abs photo" style="left:341px;top:1424px;width:251px;height:399px;background:linear-gradient(160deg,#3c3c3c,#a6a6a6 45%,#474747 75%,#5a5a5a)" role="img" aria-label="Photo of jackets on a rack"></div>
<div class="abs dark-card" style="left:609px;top:1424px;width:516px;height:399px">
  <h3 style="position:absolute;left:29px;top:10px;font-size:40px;font-weight:600">MISSION</h3>
  <p style="position:absolute;left:29px;top:68px;width:460px;font-size:19px;line-height:28px">VELMORA is a manufacturing company for Ready-to-wear, situated in Valeni, a city with a rich tradition in the clothing industry.</p>
  <div class="abs pill" style="left:32px;top:163px;width:132px;height:37px">View More</div>
  <h3 style="position:absolute;left:29px;top:212px;font-size:40px;font-weight:600">VISION</h3>
  <p style="position:absolute;left:29px;top:270px;width:470px;font-size:19px;line-height:28px">To be the leading destination for fashion brands who value both quality and sustainability.</p>
  <div class="abs pill" style="left:29px;top:340px;width:132px;height:37px">View More</div>
</div>

<h2 class="abs section-title" style="left:0;top:1941px">Velmora Elite Design</h2>
<div class="abs tabs">
  <div class="abs tab-active"></div>
  <span style="left:31px">Our Certifications</span>
  <span style="left:216px">Our Benefit</span>
  <span style="left:365px">Our Team</span>
  <span style="left:510px">Our Galleries</span>
</div>
<svg class="abs" style="left:28px;top:2308px" width="16" height="26" viewBox="0 0 16 26"><path d="M13 2L3 13l10 11" stroke="#222" stroke-width="2.5" fill="none"/></svg>
<svg class="abs" style="left:1156px;top:2320px" width="16" height="26" viewBox="0 0 16 26"><path d="M3 2l10 11L3 24" stroke="#222" stroke-width="2.5" fill="none"/></svg>

<div class="abs gallery-card" style="left:74px">
  <div class="img" style="background:linear-gradient(180deg,#ebebeb,#d4d4d4)" role="img" aria-label="Photo of models walking in a showroom"></div>
  <h3>Show Room</h3><p>The place where our latest designs are presented</p>
</div>
<div class="abs gallery-card" style="left:342px">
  <div class="img" style="background:linear-gradient(180deg,#bbb,#4b4b4b 60%,#727272)" role="img" aria-label="Photo of an office desk with computer screens"></div>
  <h3>Merchandisers</h3><p>Ensuring every product meets our high standards.</p>
</div>
<div class="abs gallery-card" style="left:609px">
  <div class="img" style="background:linear-gradient(180deg,#d2d2d2,#868686 60%,#575757)" role="img" aria-label="Photo of a design team fitting a dress on a mannequin"></div>
  <h3>PC,3D, CAD</h3><p>Expert in creating basic patterns and designs</p>
</div>
<div class="abs gallery-card" style="left:875px">
  <div class="img" style="background:linear-gradient(180deg,#bcbcbc 0%,#6e6e6e 45%,#505050 80%,#9a9a9a)" role="img" aria-label="Photo of a brick warehouse building with loading doors"></div>
  <h3>Warehouse</h3><p>A modern warehouse is a place for storing all materials</p>
</div>
<svg class="abs" style="left:572px;top:2595px" width="56" height="12" viewBox="0 0 56 12"><circle cx="5" cy="6" r="5" fill="#b5b5b5"/><circle cx="19" cy="6" r="5" fill="#b5b5b5"/><circle cx="33" cy="6" r="5" fill="#3a3a3a"/><circle cx="47" cy="6" r="5" fill="#b5b5b5"/></svg>

<section class="abs sustain">
  <svg class="abs" style="left:0;top:0" width="1044" height="349" viewBox="0 0 1044 349"><path d="M0 0H745 Q705 8 693 35 Q683 65 667 92 Q642 125 652 150 Q630 185 648 208 Q670 232 662 262 Q656 300 690 330 Q712 346 745 349H0z" fill="#3a3a3a"/></svg>
  <h2>Sustainability<br>Strategy</h2>
  <div class="bullet" style="left:88px;top:172px">Environment<br>strategy</div>
  <div class="bullet" style="left:295px;top:193px">Zero Waste<br>Project</div>
  <div class="bullet" style="left:479px;top:233px">Responsible<br>Sources</div>
  <div class="more">Want to<br><b style="font-weight:600">understand</b><br>more?</div>
  <p class="abs" style="left:795px;top:191px;font-size:12px">Click to find out more.</p>
  <div class="abs btn-dark" style="left:785px;top:231px;width:160px;height:37px;font-size:18px">View More</div>
</section>

<section class="abs feedback">
  <h2>Give Us Your Feedback</h2>
  <div class="field" style="top:117px;height:45px">Your Name</div>
  <div class="field" style="top:194px;height:44px;left:58px">Your Email</div>
  <div class="field" style="top:272px;height:130px">Please Tells us About your Feedback</div>
  <div class="abs btn-dark" style="left:445px;top:433px;width:124px;height:36px;font-size:19px">Submit</div>
</section>

<footer class="abs footer">
  <div class="flogo">Velmora</div>
  <div class="row" style="left:52px;top:98px">
    <svg width="20" height="24" viewBox="0 0 20 24"><path d="M10 22s-8-8-8-13a8 8 0 0116 0c0 5-8 13-8 13z" fill="none" stroke="#fff" stroke-width="2"/><circle cx="10" cy="9" r="3" fill="none" stroke="#fff" stroke-width="2"/></svg>
    <span>Strada Livezilor, No. 8, RO,<br>Valeni, Dumbrava,</span>
  </div>
  <div class="row" style="left:52px;top:168px">
    <svg width="20" height="20" viewBox="0 0 20 20"><circle cx="10" cy="11" r="7.5" fill="none" stroke="#fff" stroke-width="2"/><path d="M10 7v4l3 2M2 3l3-2M18 3l-3-2" stroke="#fff" stroke-width="2" fill="none"/></svg>
    <span>08:00 am - 04:30 pm</span>
  </div>
  <div class="links">Home<br>About Us<br>Velmora<br>Contact</div>
  <div class="row" style="left:866px;top:92px">
    <svg width="20" height="20" viewBox="0 0 24 24"><path d="M6 2l4 4-2 3c1 2 4 5 6 6l3-2 4 4-3 3C10 20 4 14 3 5z" fill="none" stroke="#fff" stroke-width="2"/></svg>
    <span>+4(0) 300 555 018</span>
  </div>
  <div class="row" style="left:866px;top:134px">
    <svg width="20" height="16" viewBox="0 0 24 18"><rect x="1" y="1" width="22" height="16" rx="2" fill="none" stroke="#fff" stroke-width="2"/><path d="M1 2l11 8 11-8" fill="none" stroke="#fff" stroke-width="2"/></svg>
    <span>info@velmorafashion.com</span>
  </div>
  <div class="social" style="left:923px" aria-label="Social link"></div>
  <div class="social" style="left:985px" aria-label="Social link"></div>
  <div class="social" style="left:1047px" aria-label="Social link"></div>
  <p class="copy">© 2024 Velmora. All rights reserved.</p>
</footer>

</body>
</html>
```